Design a box that holds medical gloves for paramedics!

We need a design for a box of gloves (nitrile gloves). We are designing this for a specific customer whose name is Borvik (their logo is attached as image000.1png). We have also attached the current design for the box which we want to change to be specific for Borvik. Everywhere you see a turtle, replace it with the Borvik logo. There should be no turtles on the box. The people who use these gloves are paramedics who work in an ambulance. The box should look TOUGH, American, and instill confidence and safety. An American flag alone or one incorporating the eagle from the company logo covering the top of the box (perhaps in the background on the top) would be a nice touch. Do not change anything on the bottom of the box, which is the side with the size chart on it. You can change background color but all the info on the bottom of the box needs to stay there. What you send back should be the box with all sides designed. We need to start showing our customer options right away for this box so please don't hesitate to start. We look forward to working with you.
Updates

The Client has changed his mind regarding the use of an American Flag. This product will be sold world wide, so NO FLAGS AT ALL. We still want the box to look TOUGH. We would like the top of the box to have the Borvik Logo very LARGE. We would like the Falcon from the logo to be incorporated somehow into the background of the box. So the whole Falcon or wings of the Borvik faded in background might be nice. The color scheme should still be black, red and white. The design should be bold and tough looking. This initial box will be used for black gloves but in the future the box may have blue gloves so we need some part/aspect of the box to be able to change color to blue or white if we change the color of gloves in the box in the future to have blue or white gloves. Please leave bottom of the box as is shown in original photo uploaded. Thanks and sorry for the change this late in the process.

Target Market(s)

The buyer of this product is a Paramedic who works on an ambulance. Medical market. EMS market.

Industry/Entity Type

Medical

Font styles to use
Sans Serif

Colors
ec1f27
ffffff
1b1b1b

Requirements
Must have
• American Flag
• Patriotic
• Borvik Logo in several places
• Look tough
• Color scheme should be Black, Red and White.

```html
<!DOCTYPE html>
<html lang="en">
<head>
<meta charset="utf-8">
<title>Borvik Nitrile Examination Gloves – Box Panels</title>
<link rel="stylesheet" href="https://fonts.googleapis.com/css2?family=Open+Sans:wght@400;600;700;800&display=swap">
<style>
  :root {
    --stage: #e0e1cc;
    --ink: #1b1b1b;
    --black: #151515;
    --charcoal: #2a2a2a;
    --grey: #9e9e9e;
    --grey-light: #a9a9a9;
    --red: #ec1f27;
    --white: #ffffff;
    --glove-color: #1d2a9a;
    --flag-navy: #2c3a63;
    --flag-red: #8e2a33;
  }
  * { box-sizing: border-box; margin: 0; padding: 0; }
  html, body { width: 1200px; height: 904px; overflow: hidden; }
  body {
    background: var(--stage);
    font-family: "Open Sans", Arial, sans-serif;
    color: var(--ink);
    position: relative;
  }
  .panel { position: absolute; overflow: hidden; }

  /* ---------- Top panel ---------- */
  .top-panel {
    left: 60px; top: 60px; width: 1080px; height: 420px;
    background: linear-gradient(90deg, var(--charcoal) 0%, var(--black) 40%, #262626 58%, var(--grey) 58%);
  }
  .top-art {
    position: absolute; left: 0; top: 0; width: 470px; height: 100%;
    background:
      linear-gradient(90deg, rgba(21,21,21,0) 55%, var(--black) 100%),
      linear-gradient(180deg, var(--flag-navy) 0%, #3b3f52 35%, var(--flag-red) 55%, #3a3a3a 75%, var(--charcoal) 100%);
    opacity: .9;
  }
  .window {
    position: absolute; left: 400px; top: 140px; width: 380px; height: 150px;
    border: 1.5px solid rgba(255,255,255,.28); border-radius: 22px;
    background: rgba(255,255,255,.04);
  }
  .brand-bar {
    position: absolute; left: 520px; top: 22px; display: flex; align-items: center; gap: 26px;
  }
  .brand-square { width: 86px; height: 86px; background: var(--red); border-radius: 8px; flex: none; }
  .brand-name {
    font-weight: 800; color: var(--ink); letter-spacing: -1px; line-height: 1;
    border-top: 2px solid var(--red); border-bottom: 2px solid var(--red);
    padding: 10px 20px; white-space: nowrap;
  }
  .top-panel .brand-name { font-size: 64px; }
  .size-badge { display: flex; flex-direction: column; width: 120px; }
  .size-badge .letter {
    background: var(--red); color: var(--white); font-weight: 800; font-size: 44px;
    line-height: 1; padding: 10px 16px 8px;
  }
  .size-badge .word {
    background: var(--ink); color: var(--white); font-size: 15px; padding: 3px 16px;
  }
  .top-size { position: absolute; right: 40px; top: 140px; }
  .glove-icon { position: absolute; }
  .glove-icon svg { display: block; }
  .top-glove { left: 820px; top: 150px; }
  .features { list-style: none; text-align: right; font-weight: 600; font-size: 17px; line-height: 1.3; color: var(--ink); }
  .features li { white-space: nowrap; }
  .features li::after {
    content: ""; display: inline-block; width: 7px; height: 7px; border-radius: 50%;
    background: var(--red); margin-left: 8px; vertical-align: middle;
  }
  .top-features { position: absolute; right: 30px; top: 250px; }
  .headline { color: var(--white); font-weight: 800; white-space: nowrap; }
  .top-headline { position: absolute; left: 60px; bottom: 40px; font-size: 26px; }
  .top-headline small { display: block; font-size: 19px; font-weight: 700; margin-top: 4px; }

  /* ---------- Front panel ---------- */
  .front-panel {
    left: 60px; top: 500px; width: 800px; height: 220px;
    background: linear-gradient(90deg, var(--charcoal) 0%, var(--black) 60%, #2c2c2c 100%);
  }
  .front-count {
    position: absolute; left: 0; top: 0; width: 90px; height: 100%;
    display: flex; align-items: center; justify-content: center;
    color: var(--white); font-weight: 700; font-size: 14px;
    writing-mode: vertical-rl; transform: rotate(180deg);
  }
  .front-end {
    position: absolute; left: 90px; top: 0; width: 230px; height: 100%;
    background: var(--grey); padding: 18px 18px;
  }
  .front-end .brand-row { display: flex; align-items: center; gap: 14px; }
  .front-end .brand-square { width: 46px; height: 46px; border-radius: 5px; }
  .front-end .brand-name { font-size: 32px; padding: 4px 8px; }
  .front-end .features { position: absolute; left: 18px; bottom: 18px; font-size: 14px; text-align: left; }
  .front-end .size-badge { position: absolute; right: 18px; bottom: 18px; width: 64px; }
  .front-end .size-badge .letter { font-size: 28px; padding: 6px 10px 4px; }
  .front-end .size-badge .word { font-size: 11px; padding: 2px 10px; }
  .front-art {
    position: absolute; left: 320px; top: 0; width: 180px; height: 100%;
    background: linear-gradient(90deg, #3b3b3b, rgba(21,21,21,0));
  }
  .front-headline { position: absolute; left: 350px; bottom: 40px; font-size: 19px; }
  .front-headline small { display: block; font-size: 12px; font-weight: 600; margin-top: 4px; }

  /* ---------- End panel ---------- */
  .end-panel {
    left: 880px; top: 500px; width: 260px; height: 220px;
    background: var(--grey-light); padding: 18px;
  }
  .end-panel .brand-row { display: flex; align-items: center; gap: 14px; }
  .end-panel .brand-square { width: 54px; height: 54px; border-radius: 6px; }
  .end-panel .brand-name { font-size: 34px; padding: 4px 8px; }
  .end-glove { left: 28px; top: 100px; }
  .end-size { position: absolute; right: 18px; top: 96px; width: 86px; }
  .end-size .letter { font-size: 32px; padding: 6px 12px 4px; }
  .end-size .word { font-size: 12px; padding: 2px 12px; }
  .single-use { position: absolute; right: 18px; bottom: 14px; font-size: 11px; font-weight: 600; }
</style>
</head>
<body>

<section class="panel top-panel">
  <div class="top-art" role="img" aria-label="Faded waving flag with sketched eagle heads in the background"></div>
  <div class="window"></div>
  <div class="brand-bar">
    <span class="brand-square"></span>
    <span class="brand-name">Borvik</span>
  </div>
  <div class="glove-icon top-glove">
    <svg width="80" height="80" viewBox="0 0 40 40" fill="none" stroke="var(--glove-color)" stroke-width="1.4" stroke-linejoin="round">
      <path d="M12 38 L11 22 L6 15 Q5 12 8 13 L12 18 L12 6 Q13 4 15 6 L16 16 L17 4 Q19 2 20 4 L20 16 L22 5 Q24 3 25 6 L24 17 L27 9 Q29 7 30 10 L27 24 L26 38 Z"/>
    </svg>
  </div>
  <div class="size-badge top-size"><span class="letter">L</span><span class="word">Large</span></div>
  <ul class="features top-features">
    <li>Textured</li><li>Non-Sterile</li><li>Ambidextrous</li><li>Latex Free</li>
  </ul>
  <h1 class="headline top-headline">Nitrile Powder Free Black Examination Gloves<small>100 Gloves by Weight</small></h1>
</section>

<section class="panel front-panel">
  <p class="front-count">100 Gloves by Weight</p>
  <div class="front-end">
    <div class="brand-row"><span class="brand-square"></span><span class="brand-name">Borvik</span></div>
    <ul class="features"><li>Textured</li><li>Non-Sterile</li><li>Ambidextrous</li><li>Latex Free</li></ul>
    <div class="size-badge"><span class="letter">L</span><span class="word">Large</span></div>
  </div>
  <div class="front-art" role="img" aria-label="Faded sketched eagle head"></div>
  <h2 class="headline front-headline">Nitrile Powder Free Black Examination Gloves<small>Powder free disposable examination gloves made of soft nitrile material</small></h2>
</section>

<section class="panel end-panel">
  <div class="brand-row"><span class="brand-square"></span><span class="brand-name">Borvik</span></div>
  <div class="glove-icon end-glove">
    <svg width="56" height="56" viewBox="0 0 40 40" fill="none" stroke="var(--glove-color)" stroke-width="1.6" stroke-linejoin="round">
      <path d="M12 38 L11 22 L6 15 Q5 12 8 13 L12 18 L12 6 Q13 4 15 6 L16 16 L17 4 Q19 2 20 4 L20 16 L22 5 Q24 3 25 6 L24 17 L27 9 Q29 7 30 10 L27 24 L26 38 Z"/>
    </svg>
  </div>
  <div class="size-badge end-size"><span class="letter">L</span><span class="word">Large</span></div>
  <p class="single-use">For Single Use</p>
</section>

</body>
</html>
```